Business Card Design needed for start up company Halvora

In need of a new business card designed for a start up company based in Sydney, Halvora is a new start up innovative Company, our mission it to make property accessible for everyday Australian and to become the leading Real Estate platform in Australia. We want it to be fresh and clean.

Industry/Entity Type

Financial

Contact Information for Business Card

Section for Name
Section for Title

HALVORA - The Strength of Pooling
Mobile:
Direct:

Font styles to use
Sans Serif

Colors
33a6d7
0692cd
0255a3
ffffff

Requirements
Must have
• Logo, all business card details

```html
<!DOCTYPE html>
<html lang="en">
<head>
<meta charset="utf-8">
<title>Halvora Business Card</title>
<link rel="stylesheet" href="https://fonts.googleapis.com/css2?family=Open+Sans:wght@400;600;700;800&display=swap">
<style>
  :root {
    --stage: #d9dadc;
    --card-dark: #1c1c1e;
    --card-dark-edge: #2a2a2d;
    --card-light: #ffffff;
    --navy: #0255a3;
    --blue: #0692cd;
    --sky: #33a6d7;
    --ink-grey: #6b6b6b;
    --silver: #c9c9c9;
    --silver-dim: #8a8a8a;
  }
  * { margin: 0; padding: 0; box-sizing: border-box; }
  html, body {
    width: 1200px; height: 864px; overflow: hidden;
    background: var(--stage);
    font-family: "Open Sans", Arial, sans-serif;
  }
  .stage {
    width: 1200px; height: 864px;
    display: flex; flex-direction: column;
    align-items: center; justify-content: center; gap: 48px;
  }
  .card {
    width: 600px; height: 343px;
    position: relative;
    border-radius: 4px;
    box-shadow: 0 10px 28px rgba(0,0,0,.22);
    overflow: hidden;
  }

  /* back */
  .card--back {
    background: radial-gradient(ellipse at 50% 30%, var(--card-dark-edge), var(--card-dark) 75%);
  }
  .brand {
    display: flex; align-items: center; gap: 14px;
    position: absolute;
  }
  .brand__dot { border-radius: 50%; flex: none; }
  .brand__name { font-weight: 800; letter-spacing: .5px; line-height: 1; }

  .card--back .brand { left: 50%; top: 112px; transform: translateX(-50%); }
  .card--back .brand__dot { width: 74px; height: 74px; background: var(--silver); }
  .card--back .brand__name { font-size: 62px; color: var(--silver-dim); }
  .tagline {
    position: absolute; left: 0; right: 0; top: 242px;
    text-align: center; color: #e6e6e6; font-size: 16px; letter-spacing: .3px;
  }

  /* front */
  .card--front { background: var(--card-light); }
  .card--front .brand { right: 36px; top: 34px; gap: 10px; }
  .card--front .brand__dot { width: 56px; height: 56px; background: var(--blue); }
  .card--front .brand__name { font-size: 46px; color: var(--navy); }

  .person { position: absolute; left: 40px; top: 150px; }
  .person__name { font-size: 24px; font-weight: 700; color: var(--navy); line-height: 1.1; }
  .person__title { font-size: 17px; color: var(--ink-grey); margin-top: 2px; }

  .rule {
    position: absolute; left: 40px; right: 36px; top: 212px;
    height: 1.5px; background: var(--navy);
  }

  .contacts { position: absolute; left: 40px; top: 224px; list-style: none; }
  .contacts li {
    display: flex; align-items: center; gap: 10px;
    font-size: 18px; color: var(--ink-grey); line-height: 24px;
  }
  .contacts svg { width: 14px; height: 14px; flex: none; fill: var(--blue); }

  .address {
    position: absolute; right: 36px; top: 228px;
    text-align: right; font-size: 16px; color: var(--ink-grey); line-height: 22px;
  }
</style>
</head>
<body>
<main class="stage">

  <section class="card card--back" aria-label="Card back">
    <div class="brand">
      <span class="brand__dot"></span>
      <span class="brand__name">HALVORA</span>
    </div>
    <p class="tagline">The Strength of Pooling</p>
  </section>

  <section class="card card--front" aria-label="Card front">
    <div class="brand">
      <span class="brand__dot"></span>
      <span class="brand__name">HALVORA</span>
    </div>

    <div class="person">
      <p class="person__name">John Smith</p>
      <p class="person__title">President</p>
    </div>

    <div class="rule"></div>

    <ul class="contacts">
      <li>
        <svg viewBox="0 0 24 24" aria-hidden="true"><path d="M6.6 10.8a15.1 15.1 0 0 0 6.6 6.6l2.2-2.2c.3-.3.7-.4 1-.2 1.1.4 2.3.6 3.6.6.6 0 1 .4 1 1V20c0 .6-.4 1-1 1A17 17 0 0 1 3 4c0-.6.4-1 1-1h3.5c.6 0 1 .4 1 1 0 1.3.2 2.5.6 3.6.1.3 0 .7-.2 1z"/></svg>
        01 012-345-6789
      </li>
      <li>
        <svg viewBox="0 0 24 24" aria-hidden="true"><path d="M7 1h10a2 2 0 0 1 2 2v18a2 2 0 0 1-2 2H7a2 2 0 0 1-2-2V3a2 2 0 0 1 2-2zm0 3v14h10V4zm5 15.5a1 1 0 1 0 0 2 1 1 0 0 0 0-2z"/></svg>
        01 012-345-6780
      </li>
      <li>
        <svg viewBox="0 0 24 24" aria-hidden="true"><path d="M2 5h20v14H2zm2 2v.4l8 5.3 8-5.3V7zm16 2.8-8 5.3-8-5.3V17h16z"/></svg>
        info@yourwebsite.com
      </li>
      <li>
        <svg viewBox="0 0 24 24" aria-hidden="true"><path d="M12 2a10 10 0 1 0 0 20 10 10 0 0 0 0-20zm6.9 6h-2.9a15.7 15.7 0 0 0-1.4-3.6A8 8 0 0 1 18.9 8zM12 4c.8 1.2 1.5 2.5 1.9 4h-3.8c.4-1.5 1.1-2.8 1.9-4zM4.3 14a8.2 8.2 0 0 1 0-4h3.4a16.5 16.5 0 0 0 0 4zm.8 2h2.9c.3 1.3.8 2.5 1.4 3.6A8 8 0 0 1 5.1 16zM8 8H5.1a8 8 0 0 1 4.3-3.6C8.8 5.5 8.3 6.7 8 8zm4 12c-.8-1.2-1.5-2.5-1.9-4h3.8c-.4 1.5-1.1 2.8-1.9 4zm2.3-6H9.7a14.7 14.7 0 0 1 0-4h4.6a14.7 14.7 0 0 1 0 4zm.3 5.6c.6-1.1 1.1-2.3 1.4-3.6h2.9a8 8 0 0 1-4.3 3.6zm1.7-5.6a16.5 16.5 0 0 0 0-4h3.4a8.2 8.2 0 0 1 0 4z"/></svg>
        yourwebsite.com
      </li>
    </ul>

    <p class="address">Street Name, Suite 100<br>State, Zip Code, Country</p>
  </section>

</main>
</body>
</html>
```